VELTAR WEBSITE

need to create a new website for VELTAR ltd
the company deals with all aspects of safety products & safety wear
we need a simple website to show
ideas can be taken from following website whose products we shall distribute in kenya
www.kwr.co.uk
www.dorvik.eu
www.brimtoolsupplyco.com
www.gardvalewerks.co.za

we need following tabs
1) home - basic company information
2) products - broken down to following categories ie gloves, head protection, ear protection, mouth protection, foot protection
3) contacts

the company profile is a reputable company dealing with all aspects of safety, HSE (health and safety equipment), and PPE (personal protective equipment)

the website should have the dorvik logo for which we are an authorized distributor.
the dorvi industrial range writeup can be picked from their website
Updates

Dear Designers, i shall be able to choose a final design in 2 weeks, sorry i have not been able to finalise this due to a personal reason

Target Market(s)

the buyers are all types of industry who care for their employees safety

Industry/Entity Type

Industrial

Requirements
Must have
• clean look, fresh look, user freindly
Nice to have
• clear images, quick links etc

```html
<!DOCTYPE html>
<html lang="en">
<head>
<meta charset="utf-8">
<title>VELTAR – Specialized Protective &amp; Industrial Products</title>
<link href="https://fonts.googleapis.com/css2?family=Roboto:wght@300;400;500;700&display=swap" rel="stylesheet">
<style>
  :root {
    --gold: #e0a526;
    --gold-dark: #c98f12;
    --band: #ececec;
    --page: #f4f4f4;
    --white: #ffffff;
    --text: #555555;
    --text-dark: #333333;
    --footer: #e6e6e6;
    --brand-blue: #1d5c9e;
  }
  * { margin: 0; padding: 0; box-sizing: border-box; }
  html, body { width: 863px; height: 1200px; overflow: hidden; }
  body {
    font-family: "Roboto", Arial, sans-serif;
    background: var(--page);
    color: var(--text);
    position: relative;
  }
  .top-band { position: absolute; left: 0; top: 0; width: 863px; height: 371px; background: var(--band); }

  .brand { position: absolute; left: 62px; top: 40px; display: flex; align-items: center; gap: 10px; }
  .brand-square { width: 30px; height: 30px; background: var(--gold); }
  .brand-name { font-size: 30px; font-weight: 700; color: var(--text-dark); letter-spacing: 1px; }

  .search { position: absolute; left: 614px; top: 29px; width: 186px; height: 23px; background: var(--white); border: 1px solid #d8d8d8; font-size: 10px; color: #888; padding: 5px 8px; }
  .search svg { position: absolute; right: 7px; top: 6px; }

  .main-nav { position: absolute; top: 84px; left: 0; width: 863px; font-size: 12.5px; color: var(--text-dark); }
  .main-nav a { position: absolute; text-decoration: none; color: inherit; white-space: nowrap; }
  .main-nav .active::after { content: ""; position: absolute; left: -4px; right: -4px; top: 22px; height: 3px; background: var(--gold); }

  .hero { position: absolute; left: 62px; top: 129px; width: 738px; height: 291px; background: var(--white); }
  .hero h1 { position: absolute; left: 26px; top: 88px; font-size: 21px; font-weight: 500; color: var(--gold); }
  .hero p { position: absolute; left: 26px; top: 128px; font-size: 12px; line-height: 26px; color: var(--text-dark); letter-spacing: 0.2px; }
  .shop-btn { position: absolute; left: 28px; top: 188px; width: 98px; height: 29px; background: var(--gold); border-bottom: 2px solid var(--gold-dark); color: var(--text-dark); font-size: 12px; text-align: center; line-height: 28px; }
  .hero-dots { position: absolute; left: 29px; top: 259px; display: flex; gap: 4px; }
  .hero-dots span { width: 6px; height: 6px; border-radius: 50%; background: var(--text-dark); }
  .hero-dots span.on { background: var(--white); border: 1px solid var(--text-dark); }
  .hero-visual { position: absolute; left: 350px; top: 22px; width: 378px; height: 254px; background: linear-gradient(135deg, #f5c98f 0%, #f08a30 40%, #f2b43c 70%, #f6e3a8 100%); }
  .hero-shadow { position: absolute; left: 62px; top: 420px; width: 738px; height: 38px; background: radial-gradient(ellipse at 50% 0%, rgba(0,0,0,0.22), rgba(0,0,0,0) 70%); }

  .feature { position: absolute; top: 465px; width: 230px; text-align: center; }
  .feature svg { display: block; margin: 0 auto; }
  .feature h2 { margin-top: 10px; font-size: 16px; font-weight: 400; color: var(--gold); }
  .feature p { margin-top: 8px; font-size: 10.5px; font-weight: 300; line-height: 15.5px; color: var(--text); letter-spacing: 0.3px; }

  .section-title { position: absolute; left: 62px; top: 630px; font-size: 16px; font-weight: 400; color: var(--gold); }
  .product-tile { position: absolute; top: 672px; width: 176px; height: 147px; overflow: hidden; border: 1px solid #d0d0d0; }
  .product-tile .caption { position: absolute; left: 0; bottom: 0; width: 100%; height: 37px; background: rgba(40,40,40,0.55); color: var(--white); font-size: 15px; padding: 9px 12px; }

  .divider { position: absolute; left: 62px; top: 866px; width: 738px; height: 26px; background: radial-gradient(ellipse at 50% 0%, rgba(0,0,0,0.08), rgba(0,0,0,0) 70%); }

  .welcome-visual { position: absolute; left: 62px; top: 921px; width: 240px; height: 125px; background: linear-gradient(100deg, #f2c21b 0%, #d99a1a 45%, #8a5a1e 100%); }
  .welcome { position: absolute; left: 350px; top: 919px; width: 446px; }
  .welcome h2 { font-size: 17.5px; font-weight: 400; color: var(--gold); }
  .welcome p { margin-top: 9px; font-size: 9.6px; line-height: 15.5px; color: var(--text); }
  .welcome p + p { margin-top: 5px; }

  .site-footer { position: absolute; left: 0; top: 1103px; width: 863px; height: 97px; background: var(--footer); }
  .footer-links { position: absolute; left: 63px; top: 29px; font-size: 9.5px; line-height: 24px; color: var(--text-dark); }
  .partner-name { position: absolute; left: 390px; top: 22px; font-size: 36px; font-weight: 500; color: var(--brand-blue); }
  .social { position: absolute; left: 670px; top: 36px; display: flex; gap: 9px; }
  .social span { width: 26px; height: 26px; }
</style>
</head>
<body>
  <div class="top-band"></div>

  <header>
    <div class="brand"><span class="brand-square"></span><span class="brand-name">VELTAR</span></div>
    <div class="search">Search..
      <svg width="10" height="10" viewBox="0 0 10 10"><circle cx="4" cy="4" r="3" fill="none" stroke="#999" stroke-width="1.3"/><line x1="6.2" y1="6.2" x2="9" y2="9" stroke="#999" stroke-width="1.5"/></svg>
    </div>
    <nav class="main-nav">
      <a class="active" style="left:337px">HOME</a>
      <a style="left:414px">ABOUT US</a>
      <a style="left:516px">PRODUCTS</a>
      <a style="left:624px">BROCHURES</a>
      <a style="left:741px">CONTACT</a>
    </nav>
  </header>

  <section class="hero">
    <h1>CLARITAS EST ETIAM PROCES</h1>
    <p>TYPI NON HABENT CLARITATEM INSITAM; EST USUS<br>LEGENTIS IN IIS QUI FACIT EORUM CLARITATEM.</p>
    <div class="shop-btn">SHOP NOW</div>
    <div class="hero-dots"><span class="on"></span><span></span><span></span><span></span></div>
    <div class="hero-visual" role="img" aria-label="Photo of an orange hard hat, safety glasses, work gloves and yellow ear defenders"></div>
  </section>
  <div class="hero-shadow"></div>

  <section class="feature" style="left:62px">
    <svg width="44" height="44" viewBox="0 0 44 44">
      <path d="M22 6 L42 17 L22 28 L2 17 Z" fill="#e0a526"/>
      <path d="M4 23 L22 33 L40 23" fill="none" stroke="#e0a526" stroke-width="3"/>
      <path d="M4 29 L22 39 L40 29" fill="none" stroke="#e0a526" stroke-width="3"/>
    </svg>
    <h2>SAFETY PRODUCTS</h2>
    <p>Lorem ipsum dolor sit amet adipis<br>msan. Morbi ut elit utipsum tristiquea<br>Pellentesque habitant morbi.</p>
  </section>
  <section class="feature" style="left:326px">
    <svg width="44" height="44" viewBox="0 0 44 44">
      <g fill="none" stroke="#e0a526" stroke-width="2.2">
        <path d="M19 3 h6 l1 5 l4 2 l4-3 l4 4 l-3 4 l2 4 l5 1 v6 l-5 1 l-2 4 l3 4 l-4 4 l-4-3 l-4 2 l-1 5 h-6 l-1-5 l-4-2 l-4 3 l-4-4 l3-4 l-2-4 l-5-1 v-6 l5-1 l2-4 l-3-4 l4-4 l4 3 l4-2 Z"/>
        <circle cx="22" cy="22" r="8"/><circle cx="22" cy="22" r="4"/>
      </g>
    </svg>
    <h2>SAFETY WEAR</h2>
    <p>Lorem ipsum dolor sit amet adipis<br>msan. Morbi ut elit utipsum tristiquea<br>Pellentesque habitant morbi.</p>
  </section>
  <section class="feature" style="left:573px">
    <svg width="44" height="44" viewBox="0 0 44 44">
      <g stroke="#e0a526" stroke-linecap="round">
        <line x1="10" y1="34" x2="32" y2="12" stroke-width="5"/>
        <line x1="12" y1="12" x2="34" y2="34" stroke-width="5"/>
        <circle cx="34" cy="10" r="5" fill="none" stroke-width="4"/>
        <line x1="8" y1="8" x2="14" y2="14" stroke-width="6"/>
      </g>
    </svg>
    <h2>TOOL DIVISION</h2>
    <p>Lorem ipsum dolor sit amet adipis<br>msan. Morbi ut elit utipsum tristiquea<br>Pellentesque habitant morbi.</p>
  </section>

  <h2 class="section-title">OUR PRODUCTS</h2>
  <div class="product-tile" style="left:63px; background:linear-gradient(135deg,#4a4a40,#777766 60%,#9a9a8a);" role="img" aria-label="Yellow ear defenders and foam ear plugs">
    <div class="caption">Ear Protection</div>
  </div>
  <div class="product-tile" style="left:251px; background:linear-gradient(135deg,#3a2f2c,#8b7a72 50%,#d8d8d8);" role="img" aria-label="Worker wearing a clear face shield">
    <div class="caption">Face Protection</div>
  </div>
  <div class="product-tile" style="left:438px; background:linear-gradient(160deg,#f2c21b,#c48a1a 45%,#3a2a20);" role="img" aria-label="Worker wearing a yellow hard hat and safety glasses">
    <div class="caption">Head Protection</div>
  </div>
  <div class="product-tile" style="left:625px; background:linear-gradient(135deg,#1f3d36,#2f9b86 50%,#cfd8d8);" role="img" aria-label="Hands in green chemical-resistant gloves">
    <div class="caption">Hand Protection</div>
  </div>

  <div class="divider"></div>

  <div class="welcome-visual" role="img" aria-label="Yellow hard hat resting on leather work gloves"></div>
  <section class="welcome">
    <h2>Welcome to VELTAR</h2>
    <p>Vivamus sagittis lacus vel augue laoreet rutrum faucibus dolor auctor. Aenean lacinia bibendum a sed conisectetur. Because we think it's time for a new exciting challenge! Are you ready for an nture to remember for a lifetime? Accusantium quam, ultricies eget tempor id, aliquam eget nibh Maecen aliquam, risus at sempe</p>
    <p>A program's rankings can be a key factor in choosing an accredited online college. Rankings pro vide an objective look at a program based on quantifiable factors, such as cost, graduation.</p>
  </section>

  <footer class="site-footer">
    <div class="footer-links">Privacy Policy | Terms and Conditions<br>Copyrights 2013. All Rights Reserved.</div>
    <div class="partner-name">Dorvik</div>
    <div class="social">
      <span style="background:#3b5998"></span>
      <span style="background:#2aa9e0"></span>
      <span style="background:#f26522"></span>
      <span style="background:#d62d2d"></span>
    </div>
  </footer>
</body>
</html>
```